first fantastic look and impression

We are looking for a concept for letterhead, business card, emailfooter and template for invoices or offers for our company in the consultation business.
The dancer is a symbol who we are: it looks simple, but there is a lot of hard work and many years of training in this movement. The look is also what we want: elegant, modern, strong, with a touch of extravaganza
Target Market(s)
Hotelbusiness , Consulting
Font styles to use
Sans Serif
Other font styles liked:
- please give us a option we are open
Requirements
Must have
- We are not typical consultants but sparring partners and coaches for the hotel and that should also be expressed in the design. Maybe there is an icon that supports the whole thing. We are more modern and bolder than our industry colleagues.
we are modern, fresh, agile, fast
Nice to have
- a icon

```html
<!DOCTYPE html>
<html lang="en">
<head>
<meta charset="utf-8">
<title>Brunnhofer Coaching — Business Card</title>
<link href="https://fonts.googleapis.com/css2?family=Montserrat:wght@600&family=Roboto:wght@400&display=swap" rel="stylesheet">
<style>
  :root {
    --backdrop: #d2d6d7;
    --paper: #f1f0ec;
    --ink: #141414;
    --ink-soft: #2a2a2a;
    --night: #0e0e0f;
    --silver: #dedede;
  }
  * { box-sizing: border-box; margin: 0; padding: 0; }
  html, body { width: 1200px; height: 1050px; overflow: hidden; }
  body {
    background: var(--backdrop);
    display: flex;
    flex-direction: column;
    align-items: center;
    justify-content: center;
    gap: 46px;
  }
  .card {
    width: 720px;
    height: 440px;
    position: relative;
  }
  .card--front { background: var(--paper); color: var(--ink); }
  .card--back { background: var(--night); color: var(--silver); }

  .brand-name {
    font-family: "Montserrat", sans-serif;
    font-weight: 600;
    line-height: 1.15;
    text-align: center;
  }

  /* Front */
  .front-brand {
    position: absolute;
    left: 58px; top: 110px;
    width: 250px; height: 190px;
    display: flex;
    align-items: center;
    justify-content: center;
  }
  .front-brand .brand-name { font-size: 32px; }
  .divider {
    position: absolute;
    left: 340px; top: 110px;
    width: 2px; height: 190px;
    background: var(--ink);
  }
  .contact {
    position: absolute;
    left: 372px; top: 120px;
  }
  .contact__name {
    font-family: "Montserrat", sans-serif;
    font-weight: 600;
    font-size: 20px;
    text-transform: uppercase;
  }
  .contact__role {
    font-family: "Montserrat", sans-serif;
    font-weight: 600;
    font-size: 15px;
    color: var(--ink-soft);
    margin-bottom: 16px;
  }
  .contact__list { list-style: none; }
  .contact__item {
    display: flex;
    align-items: center;
    gap: 8px;
    font-family: "Roboto", sans-serif;
    font-size: 17px;
    line-height: 27px;
  }
  .contact__icon { width: 16px; height: 16px; flex: none; }

  /* Back */
  .back-brand {
    position: absolute;
    inset: 0;
    display: flex;
    align-items: center;
    justify-content: center;
  }
  .back-brand .brand-name { font-size: 56px; }
</style>
</head>
<body>

  <section class="card card--front" aria-label="Business card front">
    <div class="front-brand">
      <p class="brand-name">Brunnhofer<br>Coaching</p>
    </div>
    <div class="divider"></div>
    <div class="contact">
      <p class="contact__name">Lena Marquardt</p>
      <p class="contact__role">Managing Director</p>
      <ul class="contact__list">
        <li class="contact__item">
          <svg class="contact__icon" viewBox="0 0 16 16" aria-hidden="true"><path d="M3.5 1.5l2.5 0.2 1 3.2-1.6 1.2a8 8 0 0 0 4.5 4.5l1.2-1.6 3.2 1 .2 2.5c-.4 1-1.5 1.7-2.6 1.5C6.5 13.3 2.7 9.5 2 4.1c-.2-1.1.5-2.2 1.5-2.6z" fill="currentColor"/></svg>
          +43 555 010022
        </li>
        <li class="contact__item">
          <svg class="contact__icon" viewBox="0 0 16 16" aria-hidden="true"><rect x="1" y="3" width="14" height="10" fill="currentColor"/><path d="M1.5 3.5L8 9l6.5-5.5" fill="none" stroke="#f1f0ec" stroke-width="1.3"/></svg>
          info@brunnhofercoaching.com
        </li>
        <li class="contact__item">
          <svg class="contact__icon" viewBox="0 0 16 16" aria-hidden="true"><g fill="none" stroke="currentColor" stroke-width="1.4"><circle cx="8" cy="8" r="6.3"/><ellipse cx="8" cy="8" rx="2.8" ry="6.3"/><path d="M1.7 8h12.6M2.8 4.8h10.4M2.8 11.2h10.4"/></g></svg>
          www.brunnhofercoaching.com
        </li>
        <li class="contact__item">
          <svg class="contact__icon" viewBox="0 0 16 16" aria-hidden="true"><path d="M8 1a5 5 0 0 0-5 5c0 3.6 5 9 5 9s5-5.4 5-9a5 5 0 0 0-5-5zm0 7a2 2 0 1 1 0-4 2 2 0 0 1 0 4z" fill="currentColor"/></svg>
          Talheim/Austria
        </li>
      </ul>
    </div>
  </section>

  <section class="card card--back" aria-label="Business card back">
    <div class="back-brand">
      <p class="brand-name">Brunnhofer<br>Coaching</p>
    </div>
  </section>

</body>
</html>
```